Frozen Yogurt Website

I need a new website based in Sydney Quenby Wharf. Our products are:

Frozen Yogurt
Smoothies
Organic Acai Bowls / Smoothies

we have professional photos of gourmet fruit and toppings in high resolution
we have the logo
we just need a web designer

no ecommerce required. Just promotional website:

following pages are needed:

About Us
Contact Us
Frozen Yogurt
Toppings
Smoothies
Acai Bowls

examples of websites we like:
http://www.velmarotrik.com
http://brantelofarmhaus.com.au/
http://www.pelvu.com.au

any questions please feel free to ask

Target Market(s)

healthy and organic food lovers
Frozen yogurt / desert eaters
tourist in quenby wharf

Industry/Entity Type

Promotional

Requirements
Should not have
• no ecommerce required

```html
<!DOCTYPE html>
<html lang="en">
<head>
<meta charset="utf-8">
<title>Velmiro – Authentic Frozen Yogurt</title>
<link href="https://fonts.googleapis.com/css2?family=Ubuntu:wght@400;500;700&family=Open+Sans:ital,wght@0,300;0,400;1,400&display=swap" rel="stylesheet">
<style>
  :root {
    --orange: #f47a3e;
    --green: #a8cf2e;
    --green-light: #cbe36a;
    --green-dark: #8fb31e;
    --lime-ring: #b5d334;
    --text-dark: #3f3f3f;
    --text-body: #6a6a6a;
    --nav-text: #4a5a1a;
    --rule: #d8d8d8;
    --white: #ffffff;
  }
  * { margin: 0; padding: 0; box-sizing: border-box; }
  h1, h2 { font-weight: 400; }
  html, body { width: 1200px; height: 999px; overflow: hidden; background: var(--white); }
  body { position: relative; font-family: "Open Sans", sans-serif; color: var(--text-body); }

  .scallop-edge {
    position: absolute; top: 0; left: 0; width: 1200px; height: 15px;
    background:
      linear-gradient(var(--orange), var(--orange)) top / 100% 6px no-repeat,
      radial-gradient(circle at 50% 5px, var(--orange) 7px, transparent 7.5px) 0 0 / 14px 15px repeat-x;
  }

  .social-links { position: absolute; top: 58px; left: 962px; display: flex; gap: 8px; list-style: none; }
  .social-links li { width: 29px; height: 29px; border-radius: 3px; background: #c9c9c9; }

  .ribbon-tail { position: absolute; top: 100px; }
  .ribbon-tail--left { left: 22px; }
  .ribbon-tail--right { left: 1070px; }

  .main-nav {
    position: absolute; top: 108px; left: 80px; width: 1024px; height: 54px;
    background: linear-gradient(var(--green-light), var(--green) 55%, var(--green-dark));
    box-shadow: 0 2px 3px rgba(0,0,0,.18);
  }
  .main-nav ul { list-style: none; position: absolute; top: 0; height: 54px; display: flex; }
  .main-nav .nav-left { left: 0; }
  .main-nav .nav-right { right: 0; }
  .main-nav li {
    height: 54px; line-height: 56px; padding: 0 14px;
    font-family: "Ubuntu", sans-serif; font-weight: 400; font-size: 18px; letter-spacing: .4px; color: var(--nav-text);
    border-left: 1px solid rgba(255,255,255,.45);
    box-shadow: inset 1px 0 0 rgba(100,130,20,.35);
  }
  .main-nav .nav-left li:first-child { border-left: 0; box-shadow: none; padding-left: 31px; }
  .main-nav .nav-right li:first-child { border-left: 0; box-shadow: none; padding-left: 30px; }
  .main-nav .nav-right li:last-child { padding-right: 31px; }

  .brand-badge {
    position: absolute; top: 40px; left: 498px; width: 190px; height: 190px; border-radius: 50%;
    background: rgba(255,255,255,.85); z-index: 3;
    display: flex; align-items: center; justify-content: center;
  }
  .brand-badge__ring {
    width: 170px; height: 170px; border-radius: 50%; background: var(--white);
    border: 6px solid var(--lime-ring);
    display: flex; align-items: center; justify-content: center;
  }
  .brand-badge__name { font-family: "Ubuntu", sans-serif; font-size: 30px; color: var(--text-dark); }

  .hero-slider {
    position: absolute; top: 160px; left: 80px; width: 1026px; height: 450px;
    background: radial-gradient(ellipse at 55% 45%, #d9d8d6, #c4c3c1 70%, #b9b8b6);
    border: 1px solid #e4e4e4;
  }
  .hero-slider__tab { position: absolute; left: 455px; bottom: -1px; }
  .hero-slider__dots { position: absolute; left: 484px; bottom: 11px; display: flex; gap: 4px; }
  .hero-slider__dots span { width: 12px; height: 12px; border-radius: 50%; background: #c4c4c4; }
  .hero-slider__dots span.is-active { background: var(--green); }

  .welcome { position: absolute; top: 648px; left: 80px; width: 420px; }
  .welcome__kicker { font-family: "Ubuntu", sans-serif; font-weight: 400; font-size: 28px; color: #4a4a4a; line-height: 32px; }
  .welcome__title { font-family: "Ubuntu", sans-serif; font-weight: 700; font-size: 40px; color: var(--orange); line-height: 48px; letter-spacing: .3px; white-space: nowrap; }
  .welcome__lead { margin: 7px 0 0 4px; font-weight: 300; font-size: 15px; line-height: 22px; color: #666; }
  .welcome__body { margin: 5px 0 0 4px; font-weight: 300; font-size: 12.5px; line-height: 22px; color: #707070; }

  .special { position: absolute; top: 646px; left: 509px; }
  .special__title { font-family: "Ubuntu", sans-serif; font-weight: 400; font-size: 26px; color: var(--green); line-height: 34px; }
  .special__frame {
    margin-top: 7px; width: 287px; height: 178px; padding: 7px;
    background: var(--white); border: 1px solid #e2e2e2; box-shadow: 0 1px 3px rgba(0,0,0,.08);
  }
  .special__photo { width: 100%; height: 100%; background: linear-gradient(135deg, #5a3e2c, #7a5a40 55%, #4a3324); }

  .testimonial { position: absolute; top: 653px; left: 817px; width: 290px; }
  .testimonial__box { background: var(--orange); border-radius: 3px; height: 188px; padding: 16px 18px 0 26px; position: relative; }
  .testimonial__box::after {
    content: ""; position: absolute; bottom: -15px; left: 222px;
    border-top: 15px solid var(--orange); border-right: 15px solid transparent;
  }
  .testimonial__title { font-family: "Ubuntu", sans-serif; font-weight: 400; font-size: 25px; color: var(--white); line-height: 30px; margin-left: -1px; }
  .testimonial__quote { font-style: italic; font-size: 12.5px; line-height: 22px; color: var(--white); margin-top: 1px; }
  .testimonial__author { text-align: right; margin: 16px 19px 0 0; font-size: 13px; color: #666; }

  .site-footer {
    position: absolute; top: 907px; left: 82px; width: 1024px; height: 40px;
    border-top: 1px solid var(--rule); font-size: 12px; color: #555;
  }
  .site-footer__legal { position: absolute; left: 3px; top: 26px; text-transform: uppercase; }
  .site-footer__copyright { position: absolute; right: 4px; top: 26px; }
</style>
</head>
<body>
  <div class="scallop-edge"></div>

  <ul class="social-links" aria-label="Social links">
    <li></li><li></li><li></li><li></li>
  </ul>

  <svg class="ribbon-tail ribbon-tail--left" width="80" height="52" viewBox="0 0 80 52" aria-hidden="true">
    <polygon points="0,0 80,0 80,52 0,52 22,26" fill="#b9d94a"/>
    <polygon points="58,52 80,52 80,62" fill="#7e9c1a"/>
  </svg>
  <svg class="ribbon-tail ribbon-tail--right" width="82" height="52" viewBox="0 0 82 52" aria-hidden="true">
    <polygon points="0,0 82,0 60,26 82,52 0,52" fill="#b9d94a"/>
  </svg>

  <nav class="main-nav">
    <ul class="nav-left">
      <li>Home</li><li>About Us</li><li>Smoothies</li><li>Toppings</li>
    </ul>
    <ul class="nav-right">
      <li>Frozen Yogurt</li><li>Acai Bowls</li><li>Contact Us</li>
    </ul>
  </nav>

  <div class="brand-badge">
    <div class="brand-badge__ring">
      <span class="brand-badge__name">Velmiro</span>
    </div>
  </div>

  <section class="hero-slider">
    <div role="img" aria-label="Fresh peaches, grapefruit halves, mint leaves and coconut cake pieces scattered on grey concrete" style="width:100%;height:100%"></div>
    <svg class="hero-slider__tab" width="116" height="38" viewBox="0 0 116 38" aria-hidden="true">
      <path d="M0,38 C10,38 12,24 20,14 C26,6 32,4 40,4 L76,4 C84,4 90,6 96,14 C104,24 106,38 116,38 Z" fill="#ffffff"/>
    </svg>
    <div class="hero-slider__dots">
      <span class="is-active"></span><span></span><span></span><span></span>
    </div>
  </section>

  <section class="welcome">
    <h2 class="welcome__kicker">WELCOME TO OUR</h2>
    <h1 class="welcome__title">WESBITE MAINPAGE..</h1>
    <p class="welcome__lead">Phasellus felis dolor, scelerisque a, tempus eget, lobortis id, libero. Donec scelerisque leo ac risus.</p>
    <p class="welcome__body">Praesent sit amet est. In dictum, dolor eu dictum porttitor, enim felis viverra mi, eget luctus massa purus quis odio. Etiam nulla massa, pharetra facilisis, volutpat in, imperdiet sit amet, sem.</p>
  </section>

  <section class="special">
    <h2 class="special__title">Today’s Sepcial</h2>
    <div class="special__frame">
      <div class="special__photo" role="img" aria-label="Granola, dried cranberries, apple slices and a small bowl of honey on a dark wooden table"></div>
    </div>
  </section>

  <section class="testimonial">
    <div class="testimonial__box">
      <h2 class="testimonial__title">Testimonials</h2>
      <p class="testimonial__quote">Vivamus porttitor, g, purus nisi eleifend libero, a tempus libero lectus feugiat felis. Morbi diam mauris, viverra in, gravida eu, mattis in, ante. Morbi eget arcu. Morbi porta, libero id ullamcorper nonummy,</p>
    </div>
    <p class="testimonial__author">by Author Name</p>
  </section>

  <footer class="site-footer">
    <span class="site-footer__legal">Terms of Service/Privacy Statement</span>
    <span class="site-footer__copyright">© 2013 Company Name.&nbsp; All right reserved.&nbsp; Term of Use</span>
  </footer>
</body>
</html>
```